Zilata - Sketches from a quiet road

🎨 Design Guidelines
1. Overall Impression

Dignified, spiritual, timeless

Central focus on sand dunes with footsteps as the main motif

Mood: calm, light, spirituality, hope

2. Color Scheme

Background: warm sand tones (beige, golden, brown)

Light source (sun/beam): soft gold/white

Typography: gold or warm yellow, metallic effect preferred (gold foil in print)

Spine and back cover: darker gradient from sand tones to deep blue/black for strong readability

3. Imagery

Front cover: sand dunes with clear footsteps leading towards light/horizon

No figurative depictions of people

Optional: subtle Islamic ornaments or geometric borders as a background accent

4. Typography

Title: “Zīlāta” → large, serif font, elegant, in gold

Subtitle: “Sketches From A Quiet Road” → smaller, clean & modern, also gold/white

Author: Idrīs-Wahīd Salmūn Qāzinī → bottom of the front cover, smaller size

Spine: Title + Arabic word زيلاتة vertically placed, harmonized with the style

5. Back Cover

Short blurb/description (provided by client)

Highlighted keywords in large type: "Courage. Integrity. Faith."

ISBN + barcode at the bottom left

Background: continuation of the sand texture from the front cover (with or without footsteps)

6. Finishing Options (Print)

Gold foil stamping for the title

Matte cover with selective gloss (eg on the light or ornaments)

High-quality, sturdy cover stock

Target Market(s)

Islamic

Font styles to use
Serif

Requirements
Must have
• read the guidelines!
Nice to have
• read the guidelines!
Should not have
• read the guidelines!

```html
<!DOCTYPE html>
<html lang="en">
<head>
<meta charset="utf-8">
<title>Zīlāta – Sketches From A Quiet Road</title>
<link rel="stylesheet" href="https://fonts.googleapis.com/css2?family=Noto+Serif:wght@400;500&family=Open+Sans:wght@400&family=Amiri:wght@400&display=swap">
<style>
:root{
  --page:#ffffff;
  --night-top:#252c37;
  --night-bottom:#111725;
  --gold-light:#f6e3a0;
  --gold-mid:#d4b35f;
  --gold-deep:#8d6a2a;
  --gold-text:#f2d98a;
  --sand-sky:#ecd391;
  --sand-glow:#fff6cf;
  --sand-mid:#d08a35;
  --sand-dark:#3a1a08;
  --spine-top:#5d4f33;
  --spine-mid:#a36a35;
  --spine-bottom:#1d2a4c;
  --body-text:#f3f3f3;
  --author:#ffffff;
  --subtitle-front:#5a4316;
}
*{margin:0;padding:0;box-sizing:border-box}
html,body{width:1200px;height:872px;overflow:hidden;background:var(--page)}
.cover-spread{position:absolute;left:43px;top:43px;width:1114px;height:786px}
.back-cover{position:absolute;left:0;top:0;width:524px;height:786px;overflow:hidden;
  background:radial-gradient(ellipse 55% 28% at 48% 30%, #2d3746 0%, transparent 70%),
  linear-gradient(180deg,var(--night-top) 0%,#1e2430 40%,var(--night-bottom) 100%)}
.back-dunes{position:absolute;left:0;top:280px;width:524px;height:506px;
  background:linear-gradient(180deg,rgba(70,78,95,0) 0%,rgba(70,78,95,.3) 12%,rgba(40,45,58,.25) 45%,rgba(17,23,37,0) 100%)}
.spine{position:absolute;left:524px;top:0;width:66px;height:786px;
  background:linear-gradient(180deg,var(--spine-top) 0%,#7a5d35 25%,var(--spine-mid) 45%,#8f5e35 62%,#4b3a44 80%,var(--spine-bottom) 100%)}
.front-cover{position:absolute;left:590px;top:0;width:524px;height:786px;overflow:hidden}
.front-photo{position:absolute;inset:0;
  background:radial-gradient(circle at 54% 34%, var(--sand-glow) 0%, rgba(255,240,190,.7) 8%, transparent 26%),
  linear-gradient(180deg,var(--sand-sky) 0%,#f3d993 30%,#e9aa55 38%,var(--sand-mid) 52%,#a85a1e 72%,#6a3210 88%,var(--sand-dark) 100%)}
.gold{background:linear-gradient(180deg,var(--gold-light) 0%,var(--gold-mid) 55%,var(--gold-deep) 100%);
  -webkit-background-clip:text;background-clip:text;color:transparent}
.title,.centered{position:absolute;white-space:nowrap;transform:translateX(-50%);line-height:1;font-family:"Noto Serif",serif;font-weight:400}
.front-title{left:262px;top:70px;font-size:132px;letter-spacing:2px;
  filter:drop-shadow(1px 2px 1px rgba(90,60,10,.6))}
.front-subtitle{left:262px;top:235px;font-size:28px;letter-spacing:2px;color:var(--subtitle-front)}
.author{left:262px;top:717px;font-size:21px;letter-spacing:1.8px;color:var(--author)}
.back-title{left:264px;top:113px;font-size:78px;letter-spacing:1px}
.back-subtitle{left:264px;top:208px;font-size:21px;letter-spacing:1.5px;color:var(--gold-text)}
.keywords{position:absolute;left:33px;top:287px;width:457px;white-space:nowrap;line-height:1;
  font-family:"Noto Serif",serif;font-size:29px;letter-spacing:2.1px;color:var(--gold-text)}
.blurb{position:absolute;font-family:"Open Sans",sans-serif;font-size:12px;line-height:16.6px;
  color:var(--body-text);letter-spacing:.2px}
.blurb .line{display:block;white-space:nowrap;text-align:justify;text-align-last:justify}
.blurb .line.end{text-align-last:left}
.blurb-one{left:33px;top:337px;width:457px}
.blurb-two{left:33px;top:421px;width:457px}
.blurb-three{left:140px;top:487px;width:350px;font-size:11.6px;letter-spacing:-.1px}
.author-photo{position:absolute;left:33px;top:490px;width:96px;height:92px;background:#fff}
.isbn-panel{position:absolute;left:168px;top:657px;width:187px;height:53px;background:#fff}
.spine-title{position:absolute;left:36px;top:213px;transform:translate(-50%,-50%) rotate(90deg);
  font-family:"Noto Serif",serif;font-size:54px;line-height:1;white-space:nowrap}
.spine-arabic{position:absolute;left:34px;top:587px;transform:translate(-50%,-50%) rotate(90deg);
  font-family:"Amiri",serif;font-size:46px;line-height:1;white-space:nowrap;color:var(--gold-mid)}
</style>
</head>
<body>
<div class="cover-spread">
  <section class="back-cover">
    <div class="back-dunes" role="img" aria-label="Dim night view of sand dunes with footsteps"></div>
    <h2 class="title back-title gold">Zīlāta</h2>
    <p class="centered back-subtitle">Sketches From A Quiet Road</p>
    <p class="keywords">COURAGE. INTEGRITY. FAITH</p>
    <p class="blurb blurb-one">
      <span class="line">Lorem ipsum dolor sit amet, consectetur adipiscing elit, sed do eiusmod</span>
      <span class="line">tempor incididunt ut labore et dolore magna aliqua. Quis ipsum suspendisse</span>
      <span class="line">ultrices gravida. Risus commodo viverra maecenas accumsan lacus vel facili-</span>
      <span class="line">sis. Lorem ipsum dolor sit amet, consectetur adipiscing elit, sed do eiusmod</span>
    </p>
    <p class="blurb blurb-two">
      <span class="line">Lorem ipsum dolor sit amet, consectetur adipiscing elit, sed do eiusmod</span>
      <span class="line">tempor incididunt ut labore et dolore magna aliqua. Quis ipsum suspendisse</span>
      <span class="line">ultrices gravida. Risus commodo viverra maecenas accumsan lacus vel facili-</span>
    </p>
    <div class="author-photo"></div>
    <p class="blurb blurb-three">
      <span class="line">Lorem ipsum dolor sit amet, consectetur adipiscing elit, sed</span>
      <span class="line">do eiusmod tempor incididunt ut labore et dolore magna</span>
      <span class="line">aliqua. Quis ipsum suspendisse ultrices gravida. Risus com-</span>
      <span class="line">modo viverra maecenas accumsan lacus vel facilisis. Quis</span>
      <span class="line">ipsum suspendisse ultrices gravida. Risus commodo viverra</span>
      <span class="line end">maecenas accumsan lacus vel facilisis.</span>
    </p>
    <div class="isbn-panel"></div>
  </section>

  <section class="spine">
    <span class="spine-title gold">Zīlāta</span>
    <span class="spine-arabic" lang="ar" dir="rtl">زيلاتة</span>
  </section>

  <section class="front-cover">
    <div class="front-photo" role="img" aria-label="Golden sand dunes at sunrise with a line of footsteps leading to the horizon"></div>
    <h1 class="title front-title gold">Zīlāta</h1>
    <p class="centered front-subtitle">Sketches From A Quiet Road</p>
    <p class="centered author">IDRĪS-WAHĪD SALMŪN QĀZINĪ</p>
  </section>
</div>
</body>
</html>
```